Construction company stationary design

We're wanting to develop a new professional stationary set for a newly establised property related business using our existing logo (attached). Business incorporates renovations, property investment and property development.

Specifically needing letter head, business cards, envelopes, email signature and need to get tshirt and caps embroydered.

Looking for something quite modern but professional using white, black and green.

Investment

```html
<!DOCTYPE html>
<html lang="en">
<head>
<meta charset="utf-8">
<title>Ridgeline Builds — Letterhead</title>
<link rel="stylesheet" href="https://fonts.googleapis.com/css2?family=Questrial&display=swap">
<style>
  :root {
    --backdrop: #ececec;
    --paper: #fbfbfb;
    --brand-green: #7cc62b;
    --ink: #4a4a4a;
    --rule: #8a8a8a;
  }
  * { margin: 0; padding: 0; box-sizing: border-box; }
  html, body {
    width: 1200px;
    height: 942px;
    overflow: hidden;
    background: var(--backdrop);
    font-family: "Questrial", "Century Gothic", sans-serif;
  }
  .canvas {
    position: relative;
    width: 1200px;
    height: 942px;
    display: flex;
    align-items: center;
    justify-content: center;
  }
  .letterhead {
    position: relative;
    width: 630px;
    height: 892px;
    background: var(--paper);
    box-shadow: 0 2px 10px rgba(0,0,0,0.08);
  }
  .brand {
    position: absolute;
    top: 66px;
    left: 62px;
    display: flex;
    align-items: center;
    gap: 10px;
  }
  .brand-square {
    width: 18px;
    height: 18px;
    background: var(--brand-green);
  }
  .brand-name {
    color: var(--brand-green);
    font-size: 26px;
    letter-spacing: 1px;
    text-transform: uppercase;
    white-space: nowrap;
  }
  .footer {
    position: absolute;
    left: 40px;
    right: 40px;
    bottom: 58px;
    color: var(--ink);
    font-size: 7.5px;
    line-height: 1;
    white-space: nowrap;
  }
  .footer-company {
    text-align: right;
    letter-spacing: 0.5px;
    text-transform: uppercase;
    margin-bottom: 8px;
  }
  .footer-contacts {
    display: flex;
    justify-content: space-between;
    align-items: center;
    padding-bottom: 7px;
  }
  .contact-address { flex: none; }
  .contact-group {
    display: flex;
    flex: none;
    gap: 12px;
    align-items: center;
  }
  .contact-item {
    display: flex;
    flex: none;
    align-items: center;
    gap: 4px;
    white-space: nowrap;
  }
  .contact-icon { width: 8px; height: 8px; flex: none; }
  .footer-rule {
    height: 1px;
    background: var(--rule);
  }
</style>
</head>
<body>
<main class="canvas">
  <article class="letterhead">
    <header class="brand">
      <span class="brand-square"></span>
      <span class="brand-name">Ridgeline Builds</span>
    </header>

    <footer class="footer">
      <div class="footer-company">Ridgeline Builds</div>
      <div class="footer-contacts">
        <span class="contact-address">418 Larkspur Ct, Suite 210, Aldenbrook, CO 80555</span>
        <div class="contact-group">
          <span class="contact-item">
            <svg class="contact-icon" viewBox="0 0 10 10"><rect width="10" height="10" rx="1.5" fill="var(--brand-green)"/><path d="M3 2.5c0 3 1.5 4.5 4.5 5l.6-1.2-1.4-.8-.7.7C5 5.7 4.3 5 4.1 4l.7-.7L4 1.9z" fill="#fff"/></svg>
            (555) 014-2290
          </span>
          <span class="contact-item">
            <svg class="contact-icon" viewBox="0 0 10 10"><rect width="10" height="10" rx="1.5" fill="var(--brand-green)"/><path d="M2 3h6v4H2z M2 3l3 2.2L8 3" fill="none" stroke="#fff" stroke-width="0.8"/></svg>
            hello@ridgelinebuilds.com
          </span>
          <span class="contact-item">
            <svg class="contact-icon" viewBox="0 0 10 10"><circle cx="5" cy="5" r="5" fill="var(--brand-green)"/><circle cx="5" cy="5" r="2.8" fill="none" stroke="#fff" stroke-width="0.8"/><path d="M2.2 5h5.6" stroke="#fff" stroke-width="0.8"/></svg>
            www.ridgelinebuilds.com
          </span>
        </div>
      </div>
      <div class="footer-rule"></div>
    </footer>
  </article>
</main>
</body>
</html>
```